Dental Medical History Form - Content provided

Design a medical history form for a dental practice. Content is provided so all that is needed is the formatting to make it look great and easy to read.

"Patient Information" to include all information contained in top portion of the "Patient Medical History Form" docx file.

"Medical History" should follow the formatting and content of the "Exact Medical History" file as this is what the entry fields look like in our practice software and so we would like it to match.

1st page - Patient info, allergies, medications, antibiotics, joint replacement, pregnancy.

2nd page - Do you have, or have you had, any of the following? . . . . . . .
Updates

Target Market(s)

All ages but must be clear enough for elderly to read. Use as much space as possible to keep font size bigger yet keep to two pages

Industry/Entity Type

Dental

Font styles to use
Sans Serif

Requirements
Must have
• All content provided
• Our logo at the top (file provided)
• Century Gothic Font
• Limit to two pages

```html
<!DOCTYPE html>
<html lang="en">
<head>
<meta charset="utf-8">
<title>Crestline Dental – Confidential Medical History</title>
<link href="https://fonts.googleapis.com/css2?family=Questrial&family=PT+Sans+Narrow:wght@400;700&display=swap" rel="stylesheet">
<style>
  :root{
    --backdrop:#e9e9e9;
    --paper:#ffffff;
    --ink:#2b3a48;
    --rule:#4a5662;
    --band-start:#ffffff;
    --band-end:#c9c9c9;
    --tab:#dcdcdc;
  }
  *{box-sizing:border-box;margin:0;padding:0}
  html,body{width:1200px;height:784px;overflow:hidden;background:var(--backdrop)}
  body{display:flex;align-items:center;justify-content:center;
       font-family:"PT Sans Narrow",sans-serif;color:var(--ink);font-size:10px}
  .page{position:relative;width:560px;height:764px;background:var(--paper);
        box-shadow:0 2px 6px rgba(0,0,0,.12);padding:22px 34px 18px}
  .side-tab{position:absolute;width:8px;height:44px;background:var(--tab)}
  .side-tab.left-top{left:0;top:26px}
  .side-tab.right-top{right:0;top:26px}
  .side-tab.left-bottom{left:0;bottom:86px}
  .masthead{display:flex;justify-content:space-between;align-items:flex-start}
  .brand{display:flex;align-items:center;gap:8px;font-family:"Questrial",sans-serif;
         font-size:28px;color:var(--ink);letter-spacing:.5px}
  .brand-dot{width:12px;height:12px;border-radius:50%;background:var(--ink)}
  .practice-contact{text-align:right;font-weight:700;font-size:9px;line-height:1.35}
  .practice-contact .phone{font-size:12px}
  .form-title{font-weight:700;font-size:14px;letter-spacing:3px;text-decoration:underline;
              margin:6px 0 8px}
  .row{display:flex;align-items:flex-end;gap:6px;height:21px}
  .label{white-space:nowrap;font-size:10px}
  .box{flex:1;height:14px;border:1px solid var(--rule)}
  .box.w-sm{flex:0 0 70px}
  .subhead{display:flex;gap:6px;font-size:8px;font-style:italic;height:10px;align-items:flex-end}
  .subhead span{flex:1}
  .band{margin:8px 0 4px;height:17px;display:flex;align-items:center;justify-content:center;
        font-weight:700;font-size:11px;
        background:linear-gradient(90deg,var(--band-start),var(--band-end) 48%,var(--band-start))}
  .tick{display:inline-block;width:11px;height:11px;border:1px solid var(--rule);vertical-align:middle;margin:0 4px 0 2px}
  .choices{display:flex;justify-content:space-between;height:19px;align-items:center;font-size:10px}
  .choice{white-space:nowrap}
  .line{border-bottom:1px solid var(--rule);height:19px}
  .question{display:flex;align-items:center;height:21px;gap:10px}
  .question .q{width:180px}
  .turnover{position:absolute;left:0;bottom:22px;background:linear-gradient(90deg,var(--band-end),var(--band-start));
            font-weight:700;font-size:11px;padding:3px 26px 3px 16px}
</style>
</head>
<body>
<main class="page">
  <span class="side-tab left-top"></span><span class="side-tab right-top"></span><span class="side-tab left-bottom"></span>

  <header class="masthead">
    <div class="brand"><span class="brand-name">Crestline Dental</span><span class="brand-dot"></span></div>
    <div class="practice-contact">
      <div class="phone">(02) 5550 1234</div>
      <div>Crestline Dental, 4/118 Harbour View Rd,</div>
      <div>Lindale NSW 2999</div>
    </div>
  </header>

  <h1 class="form-title">CONFIDENTIAL MEDICAL HISTORY</h1>

  <section class="patient">
    <div class="subhead"><span style="padding-left:40px">First</span><span>Middle</span><span>Last</span></div>
    <div class="row"><span class="label">Name:</span><span class="box"></span><span class="box"></span><span class="box"></span></div>
    <div class="row"><span class="label">Address:</span><span class="box"></span></div>
    <div class="row"><span class="label">DOB:</span><span class="box"></span><span class="label">Email Address:</span><span class="box"></span></div>
    <div class="row"><span class="label">Phone Number(s): Mobile:</span><span class="box"></span><span class="label">Work:</span><span class="box"></span><span class="label">Home:</span><span class="box"></span></div>
    <div class="row"><span class="label">Emergency Contact Person: Name:</span><span class="box"></span><span class="label">Relationship:</span><span class="box"></span><span class="label">Phone number:</span><span class="box"></span></div>
  </section>

  <h2 class="band">General Practitioner:</h2>
  <section class="gp">
    <div class="row"><span class="label">Name:</span><span class="box"></span><span class="label">Phone Number:</span><span class="box"></span></div>
    <div class="row"><span class="label">Practice Name:</span><span class="box"></span></div>
    <div class="row"><span class="label">Do you have a health fund with dental cover? Yes</span><span class="tick"></span><span class="label">or No</span><span class="tick"></span><span class="label">If so, what is the name of the fund?</span><span class="box"></span></div>
    <div class="row"><span class="label">Fund Number:</span><span class="box"></span><span class="label">Priority Number on card: 0<span class="tick"></span>1<span class="tick"></span>2<span class="tick"></span>3<span class="tick"></span>4<span class="tick"></span>5</span></div>
    <div class="row"><span class="label">Occupation:</span><span class="box"></span><span class="label">Referred by:</span><span class="box"></span></div>
  </section>

  <h2 class="band">Please indicate if you are allergic to any of the following:</h2>
  <section class="allergies">
    <div class="choices">
      <span class="choice">Aspirin<span class="tick"></span></span><span class="choice">Codeine<span class="tick"></span></span>
      <span class="choice">Penicillin<span class="tick"></span></span><span class="choice">Sulfites<span class="tick"></span></span>
      <span class="choice">Latex<span class="tick"></span></span><span class="choice">Local Anaesthetic<span class="tick"></span></span>
      <span class="choice">Lactose<span class="tick"></span></span><span class="choice">Nickel<span class="tick"></span></span>
    </div>
    <div class="row"><span class="label">Other:</span><span class="box"></span></div>
  </section>

  <h2 class="band">Are you currently taking, or have ever taken, any of the following medications?</h2>
  <section class="medications">
    <div class="choices">
      <span class="choice">Asthma inhaler<span class="tick"></span></span><span class="choice">Anti-epileptics<span class="tick"></span></span>
      <span class="choice">Anti-depressants<span class="tick"></span></span><span class="choice">Blood Pressure<span class="tick"></span></span>
      <span class="choice">Blood Thinners<span class="tick"></span></span><span class="choice">Bisphosphonates<span class="tick"></span></span>
    </div>
    <div class="choices">
      <span class="choice">Chemotherapy<span class="tick"></span></span><span class="choice">Insulin<span class="tick"></span></span>
      <span class="choice">Immunosuppressants<span class="tick"></span></span><span class="choice">Steroids<span class="tick"></span></span>
      <span class="choice">Oral Contraceptive<span class="tick"></span></span><span class="choice">Other<span class="tick"></span></span>
    </div>
  </section>

  <h2 class="band">Please specify medication name, dose, and frequency where possible:</h2>
  <section class="medication-notes">
    <div class="line"></div><div class="line"></div><div class="line"></div><div class="line"></div>
  </section>

  <section class="questions" style="margin-top:10px">
    <div class="question"><span class="q">Do you require antibiotic cover?</span><span>Yes<span class="tick"></span></span><span>No<span class="tick"></span></span></div>
    <div class="question"><span class="q">Have you had a joint replacement?</span><span>Yes<span class="tick"></span></span><span>No<span class="tick"></span></span></div>
    <div class="question"><span class="q">Women: &nbsp;Are you pregnant?</span><span>Yes<span class="tick"></span></span><span>No<span class="tick"></span></span><span>Possible<span class="tick"></span></span><span>or &nbsp;Breast Feeding?</span><span>Yes<span class="tick"></span></span><span>No<span class="tick"></span></span></div>
  </section>

  <div class="turnover">Please Turnover</div>
</main>
</body>
</html>
```